Detail Shop Business card design

i need a business card design for my new detailing company called 'Brisk's Polish Works'. i want an all black and white design . simple, direct and to the point. i want the designer to choose a fitting font to match the logothe front should have logo, address, phone and email and the back side should have a slogan and text indicating that we offer services on anything including cars, trucks, motorcycles and RVs. slogan will read "we take pride in your ride"
maybe also very small on the back side the IG icon with Brisks_Polish_Works

phone 208.417.6352
address 3847 E Larkin Ave
Spokane WA 99214
email: BrisksPolish@mailvexo.com

Target Market(s)

all ages , auto enthusiasts

Industry/Entity Type

Automotive

Contact Information for Business Card

the front should have logo, address, phone and email and the back side should have a slogan and text indicating that we offer services on anything including cars, trucks, motorcycles and RVs. slogan will read "we take pride in your ride"

phone 208.417.6352
address 3847 E Larkin Ave
Spokane WA 99214

Colors
000000
ffffff

Requirements
Must have
• bold font and very simple design with good spacing
Nice to have
• anything creative from the designer indicating we service any types of vehicles
Should not have
• any colors ,

```html
<!DOCTYPE html>
<html lang="en">
<head>
<meta charset="utf-8">
<title>Brisk's Polish Works – Business Card</title>
<link rel="stylesheet" href="https://fonts.googleapis.com/css2?family=Roboto+Slab:wght@400;700&family=Oswald:wght@400;600&display=swap">
<style>
  :root {
    --canvas: #e8e8e6;
    --card-front: #f4f4f4;
    --card-back: #535353;
    --ink: #1c1c1c;
    --ink-soft: #6a6a6a;
    --ink-back: #111111;
    --illustration: #1a1a1a;
  }
  * { margin: 0; padding: 0; box-sizing: border-box; }
  html, body { width: 1200px; height: 950px; overflow: hidden; background: var(--canvas); }
  .canvas { position: relative; width: 1200px; height: 950px; }

  .card {
    position: absolute;
    top: 142px;
    width: 380px;
    height: 665px;
    box-shadow: 0 4px 14px rgba(0,0,0,0.18);
  }

  /* Front */
  .card-front { left: 150px; background: var(--card-front); color: var(--ink); }
  .brand {
    position: absolute;
    top: 96px;
    right: 40px;
    display: flex;
    align-items: center;
    gap: 10px;
    font-family: "Roboto Slab", serif;
    font-weight: 700;
    font-size: 19px;
    color: var(--ink);
  }
  .brand-dot { width: 14px; height: 14px; border-radius: 50%; background: var(--ink); }
  .person { position: absolute; left: 40px; top: 360px; font-family: "Roboto Slab", serif; }
  .person-name { font-weight: 700; font-size: 21px; letter-spacing: 1px; }
  .person-role { font-weight: 700; font-size: 15px; color: var(--ink-soft); letter-spacing: 1px; margin-top: 2px; }
  .contact {
    position: absolute;
    left: 40px;
    top: 432px;
    font-family: "Roboto Slab", serif;
    font-size: 14px;
    line-height: 20px;
    color: var(--ink-soft);
  }
  .contact-address { padding-left: 26px; margin-bottom: 2px; }
  .contact-row { display: flex; align-items: center; gap: 10px; }
  .contact-row svg { width: 16px; height: 16px; flex: none; fill: var(--ink); }
  .rule { position: absolute; left: 40px; right: 40px; top: 590px; border-top: 1.5px solid var(--ink); }

  /* Back */
  .card-back { left: 670px; background: var(--card-back); overflow: hidden; }
  .back-layout {
    position: absolute;
    width: 665px;
    height: 380px;
    left: -142.5px;
    top: 142.5px;
    transform: rotate(90deg);
  }
  .vehicle-art {
    position: absolute;
    left: 70px;
    top: 50px;
    width: 520px;
    height: 190px;
    border-radius: 60px 90px 40px 40px;
    background: linear-gradient(180deg, #2a2a2a, var(--illustration));
  }
  .slogan {
    position: absolute;
    left: 70px;
    top: 258px;
    font-family: "Oswald", sans-serif;
    font-weight: 600;
    font-size: 25px;
    letter-spacing: 1px;
    color: var(--ink-back);
    padding-bottom: 6px;
    border-bottom: 1.5px solid var(--ink-back);
  }
  .services {
    position: absolute;
    left: 70px;
    top: 308px;
    font-family: "Oswald", sans-serif;
    font-weight: 400;
    font-size: 17px;
    color: var(--ink-back);
  }
</style>
</head>
<body>
<main class="canvas">

  <section class="card card-front" aria-label="Business card front">
    <div class="brand"><span class="brand-dot"></span>Brisk's Polish Works</div>

    <div class="person">
      <div class="person-name">MARK HOLLOWAY</div>
      <div class="person-role">CEO/FOUNDER</div>
    </div>

    <div class="contact">
      <div class="contact-address">3847 E Larkin Ave<br>Spokane WA 99214</div>
      <div class="contact-row">
        <svg viewBox="0 0 16 16" aria-hidden="true"><path d="M4 1l3 3-2 2c1 2 3 4 5 5l2-2 3 3-2 2C7 14 2 9 2 3z"/></svg>
        <span>208.417.6352</span>
      </div>
      <div class="contact-row">
        <svg viewBox="0 0 16 16" aria-hidden="true"><path d="M4 1h8v14H4z M5.5 2.5v10h5v-10z"/></svg>
        <span>208 553 7140</span>
      </div>
      <div class="contact-row">
        <svg viewBox="0 0 16 16" aria-hidden="true"><path d="M1 3h14v10H1z M2.5 4.5L8 9l5.5-4.5v7h-11z"/></svg>
        <span>BrisksPolish@mailvexo.com</span>
      </div>
      <div class="contact-row">
        <svg viewBox="0 0 16 16" aria-hidden="true"><circle cx="8" cy="8" r="7"/></svg>
        <span>www.briskspolish.com</span>
      </div>
    </div>

    <div class="rule"></div>
  </section>

  <section class="card card-back" aria-label="Business card back">
    <div class="back-layout">
      <div class="vehicle-art" role="img" aria-label="Black silhouette illustration of a classic hot rod car"></div>
      <div class="slogan">WE TAKE PRIDE IN YOUR RIDE</div>
      <div class="services">Services on anything including cars, trucks, motorcycles &amp; RVs</div>
    </div>
  </section>

</main>
</body>
</html>
```